Promotional business a5 Notepad design

I am looking for a custom a5 notepad design as a promotional item to give away to customers etc.
Attached will be a desk planner we had designed feel free to use as a reference.
We want the notepad to have lines running horizontal not squares like the desk planner example.

Industry/Entity Type

Hydraulic / industrial

Colors

Designer to choose colors to be used in the design.

```html
<!DOCTYPE html>
<html lang="en">
<head>
<meta charset="utf-8">
<title>Meridian Hose Supply – A5 Notepad</title>
<link rel="stylesheet" href="https://fonts.googleapis.com/css2?family=Inter:wght@400;700&display=swap">
<style>
  :root {
    --backdrop: #d9dadd;
    --paper: #f1f1f2;
    --brand-blue: #1530c0;
    --ink: #1d1d1f;
    --rule: #8c8c8e;
  }
  * { box-sizing: border-box; margin: 0; padding: 0; }
  html, body {
    width: 1200px; height: 1141px; overflow: hidden;
    background: var(--backdrop);
    font-family: "Inter", Arial, sans-serif;
  }
  .notepad-page {
    position: absolute; left: 215px; top: 30px;
    width: 769px; height: 1081px;
    background: var(--paper);
  }
  .page-frame {
    position: absolute; left: 17px; top: 16px; right: 17px; bottom: 19px;
    border: 4px solid var(--brand-blue);
  }
  .frame-gap {
    position: absolute; right: 14px; top: 66px;
    width: 10px; height: 68px;
    background: var(--paper);
  }
  .brand-mark {
    position: absolute; left: 53px; top: 64px; height: 58px;
    display: flex; align-items: center; gap: 10px;
  }
  .brand-dot {
    width: 44px; height: 44px; border-radius: 50%;
    background: var(--brand-blue);
  }
  .brand-name {
    font-weight: 700; font-size: 21px; letter-spacing: 0.5px;
    color: var(--brand-blue); text-transform: uppercase;
  }
  .contact-block {
    position: absolute; right: 54px; top: 72px;
    text-align: right; color: var(--ink);
    font-size: 11.4px; line-height: 14px;
  }
  .contact-block p:last-child { margin-top: 1px; }
  .contact-icons {
    position: absolute; left: 744px; top: 73px;
    display: flex; flex-direction: column; gap: 5px;
  }
  .contact-icons svg { width: 10px; height: 10px; display: block; fill: var(--brand-blue); }
  .writing-rules {
    position: absolute; left: 55px; top: 192px; width: 659px;
  }
  .writing-rules span {
    display: block; height: 1px; background: var(--rule);
    margin-bottom: 44.6px;
  }
</style>
</head>
<body>
  <main class="notepad-page">
    <div class="page-frame"></div>
    <div class="frame-gap"></div>

    <div class="brand-mark">
      <span class="brand-dot"></span>
      <span class="brand-name">Meridian Hose Supply</span>
    </div>

    <div class="contact-block">
      <p>0400 123 456</p>
      <p>hello@meridianhose.com.au</p>
      <p>www.meridianhose.com.au</p>
      <p>Servicing the Greater Metro area</p>
    </div>

    <div class="contact-icons">
      <svg viewBox="0 0 24 24" aria-label="Phone"><path d="M6.6 10.8a15 15 0 0 0 6.6 6.6l2.2-2.2c.3-.3.7-.4 1-.2 1.1.4 2.3.6 3.6.6.6 0 1 .4 1 1V20c0 .6-.4 1-1 1C10.6 21 3 13.4 3 4c0-.6.4-1 1-1h3.5c.6 0 1 .4 1 1 0 1.3.2 2.5.6 3.6.1.3 0 .7-.2 1z"/></svg>
      <svg viewBox="0 0 24 24" aria-label="Email"><path d="M2 5h20v14H2zm2 2v.5l8 5 8-5V7l-8 5z"/></svg>
      <svg viewBox="0 0 24 24" aria-label="Website"><path d="M12 2a10 10 0 1 0 0 20 10 10 0 0 0 0-20zm0 2c.9 1.2 1.6 2.8 1.9 4.5h-3.8C10.4 6.8 11.1 5.2 12 4zM4.3 13a8 8 0 0 1 0-2h3.8a17 17 0 0 0 0 2zm.8 2h3.4c.3 1.5.8 2.9 1.5 4a8 8 0 0 1-4.9-4zm3.4-6H5.1a8 8 0 0 1 4.9-4c-.7 1.1-1.2 2.5-1.5 4zM12 20c-.9-1.2-1.6-2.8-1.9-5h3.8c-.3 2.2-1 3.8-1.9 5zm2.1-7h-4.2a15 15 0 0 1 0-2h4.2a15 15 0 0 1 0 2zm0 6c.7-1.1 1.2-2.5 1.5-4h3.4a8 8 0 0 1-4.9 4zm1.8-6a17 17 0 0 0 0-2h3.8a8 8 0 0 1 0 2zm-.4-4c-.3-1.5-.8-2.9-1.5-4a8 8 0 0 1 4.9 4z"/></svg>
      <svg viewBox="0 0 24 24" aria-label="Location"><path d="M12 2a7 7 0 0 0-7 7c0 5 7 13 7 13s7-8 7-13a7 7 0 0 0-7-7zm0 9.5a2.5 2.5 0 1 1 0-5 2.5 2.5 0 0 1 0 5z"/></svg>
    </div>

    <div class="writing-rules">
      <span></span><span></span><span></span><span></span><span></span><span></span>
      <span></span><span></span><span></span><span></span><span></span><span></span>
      <span></span><span></span><span></span><span></span><span></span><span></span>
    </div>
  </main>
</body>
</html>
```